Corvin Ridge Software PowerPoint template

We are a software company selling endpoint visibility, access and security technology to enterprise-level IT departments.
Our technology helps organizations gain comprehensive visibility into and control over devices accessing their corporate network so they can quickly identify and address suspicious activity on the network that could lead to potential threats like data breaches.
This technology can cost organizations upwards of $1M - depending on the size of the organization. Our primary clients are Vestral 2,000 companies.
We want a professional, polished PowerPoint template that we can use for all company presentations. Please include:
Title page
Section page
General info page
Thank you page
Logo options and color specs are attached.
Please include our tagline on at least the title page: Discover the edge. Optimize the whole.
Reason: Seeking more options. Looking for a clean design that uses lots of white space.
Software

```html
<!DOCTYPE html>
<html lang="en">
<head>
<meta charset="utf-8">
<title>Agenda – Corvin Ridge Software</title>
<link rel="stylesheet" href="https://fonts.googleapis.com/css2?family=Ubuntu:wght@400;500;700&display=swap">
<style>
  :root {
    --brand-red: #9b1c20;
    --accent: #d0805e;
    --ink: #1a1a1a;
    --muted: #444444;
    --rule: #b5b5b5;
    --pattern-tone: #ececec;
    --paper: #ffffff;
  }
  * { margin: 0; padding: 0; box-sizing: border-box; }
  html, body {
    width: 1200px;
    height: 849px;
    overflow: hidden;
    background: var(--paper);
  }
  .slide {
    position: relative;
    width: 1200px;
    height: 849px;
    overflow: hidden;
    background: var(--paper);
    font-family: "Ubuntu", "Helvetica Neue", Arial, sans-serif;
    color: var(--ink);
  }
  .header-bar {
    position: absolute;
    left: 133px;
    top: 0;
    width: 7px;
    height: 86px;
    background: var(--brand-red);
  }
  .deck-title {
    position: absolute;
    left: 163px;
    top: 37px;
    font-size: 20px;
    font-weight: 400;
    line-height: 24px;
    color: var(--brand-red);
  }
  .deck-date {
    position: absolute;
    left: 163px;
    top: 63px;
    font-size: 18px;
    font-weight: 500;
    line-height: 22px;
    color: var(--ink);
  }
  .deck-date strong { font-weight: 700; }
  .corner-pattern {
    position: absolute;
    left: 820px;
    top: 0;
    width: 380px;
    height: 370px;
    background: radial-gradient(ellipse at 75% 35%, var(--pattern-tone) 0%, rgba(236,236,236,0.5) 45%, rgba(255,255,255,0) 75%);
  }
  .page-dot {
    position: absolute;
    left: 1096px;
    top: 36px;
    width: 56px;
    height: 56px;
    border-radius: 50%;
    background: var(--accent);
    color: #ffffff;
    font-size: 17px;
    font-weight: 700;
    line-height: 56px;
    text-align: center;
  }
  .slide-title {
    position: absolute;
    left: 128px;
    top: 170px;
    font-size: 72px;
    font-weight: 700;
    line-height: 80px;
    color: var(--accent);
  }
  .agenda-item {
    position: absolute;
    left: 168px;
    width: 700px;
    font-size: 20px;
    font-weight: 500;
    line-height: 26px;
    color: var(--ink);
  }
  .agenda-item::before {
    content: "";
    position: absolute;
    left: -30px;
    top: 7px;
    width: 14px;
    height: 14px;
    border-radius: 50%;
    background: var(--accent);
  }
  .item-1 { top: 291px; }
  .item-2 { top: 403px; }
  .item-3 { top: 487px; }
  .item-4 { top: 547px; }
  .item-5 { top: 635px; }
  .footer-rule {
    position: absolute;
    left: 128px;
    top: 770px;
    width: 710px;
    height: 1px;
    background: var(--rule);
  }
  .copyright {
    position: absolute;
    left: 133px;
    top: 779px;
    font-size: 12px;
    line-height: 14px;
    color: var(--muted);
  }
  .brand-name {
    position: absolute;
    left: 852px;
    top: 744px;
    display: flex;
    align-items: center;
    gap: 14px;
  }
  .brand-mark {
    width: 34px;
    height: 34px;
    border-radius: 50%;
    background: var(--accent);
  }
  .brand-word {
    font-size: 24px;
    font-weight: 500;
    line-height: 30px;
    color: var(--brand-red);
    letter-spacing: 2px;
  }
</style>
</head>
<body>
<main class="slide">
  <div class="header-bar"></div>
  <p class="deck-title">PPT HEADING GOES HERE</p>
  <p class="deck-date">FEB, <strong>2015</strong></p>

  <div class="corner-pattern" role="img" aria-label="Decorative pattern of outlined circles in the top-right corner"></div>
  <div class="page-dot">01</div>

  <h1 class="slide-title">Agenda</h1>

  <p class="agenda-item item-1">US Corporation with 16 years Lease and Loan Management Software experience US Corporation with 16 years Lease and Loan Management Software experience</p>
  <p class="agenda-item item-2">US Corporation with 16 years Lease and Loan Management Software experience US Corporation with 16 years Lease and L</p>
  <p class="agenda-item item-3">US Corporation with 16 years Lease and</p>
  <p class="agenda-item item-4">US Corporation with 16 years Lease and Loan Management Software experience US Corporation with 16 y</p>
  <p class="agenda-item item-5">US Corporation with 16 years Lease and</p>

  <div class="footer-rule"></div>
  <p class="copyright">©2015 Corvin Ridge Software</p>

  <div class="brand-name">
    <span class="brand-mark"></span>
    <span class="brand-word">CORVIN RIDGE<br>SOFTWARE</span>
  </div>
</main>
</body>
</html>
```